Business card design Needed for new logo / Construction business, home extensions and new builds

We need a business card design using our new logo files which i will attach to this project :)

We are a small construction business specialising in home extensions, new builds and property development. We are very ambitious and would appreciate professional and elegant designs for our new business card.

Very serious about using the services on MakerQuarry and recently acquired our new logo from here :)

Please get involved, i will feedback when i can as i am very busy but can respond daily, thanks

Target Market(s)

People that want to build onto their houses, new building developments or adding too their existing property

Industry/Entity Type

Construction

Contact Information for Business Card

Renwick Tolliver Construction, Lionel Ashby (Managing Director), Tel 07822254961, email - info@renwick-tolliver, www.renwick-tolliver.co.uk

Colors

Designer to choose colors to be used in the design.

Requirements
Must have
• I like a deep grey on the back please. A lot of you have provided black from and back, try mixing things up a little. The black looks cool 😎 Thanks

```html
<!DOCTYPE html>
<html lang="en">
<head>
<meta charset="utf-8">
<title>Renwick Tolliver Construction – Business Card</title>
<link href="https://fonts.googleapis.com/css2?family=Open+Sans:wght@400;600;700&display=swap" rel="stylesheet">
<style>
  :root {
    --stage: #1b1b1d;
    --card-black: #1e1e21;
    --card-black-edge: #26262a;
    --deep-grey-light: #a3a8ad;
    --deep-grey-dark: #6f7378;
    --gold: #d6a532;
    --gold-light: #f0c863;
    --silver: #d9dadc;
    --white: #f4f4f4;
    --emboss: #2a2a2e;
  }
  * { box-sizing: border-box; margin: 0; padding: 0; }
  html, body {
    width: 1200px; height: 780px; overflow: hidden;
    background: var(--stage);
    font-family: "Open Sans", Arial, sans-serif;
  }
  .canvas {
    position: relative; width: 1200px; height: 780px;
    display: flex; align-items: center; justify-content: center; gap: 40px;
  }
  .card {
    position: relative; width: 540px; height: 310px; overflow: hidden;
    box-shadow: 0 14px 30px rgba(0,0,0,.55);
  }

  /* Back */
  .card--back {
    background: linear-gradient(160deg, var(--deep-grey-light) 0%, #8d9196 55%, var(--deep-grey-dark) 100%);
  }
  .back-pattern {
    position: absolute; inset: 0;
    background: linear-gradient(160deg, rgba(255,255,255,.12), rgba(0,0,0,.12));
  }
  .back-mark {
    position: absolute; right: 22px; top: 112px;
    display: flex; align-items: center; gap: 5px;
    font-size: 7px; font-weight: 600; color: var(--white);
    letter-spacing: .04em; text-transform: uppercase;
  }
  .back-mark__square { width: 9px; height: 9px; background: var(--white); }

  /* Front */
  .card--front { background: linear-gradient(150deg, var(--card-black-edge), var(--card-black) 60%); }
  .person {
    position: absolute; top: 26px; right: 0;
    display: flex; align-items: stretch; gap: 10px;
  }
  .person__text { text-align: right; padding-top: 2px; }
  .person__name { font-size: 27px; font-weight: 700; line-height: 1; letter-spacing: .01em; }
  .person__first { color: var(--silver); }
  .person__last { color: var(--gold); }
  .person__role { font-size: 12.5px; font-weight: 600; color: var(--white); margin-top: 4px; }
  .person__bar { width: 9px; background: linear-gradient(90deg, var(--gold), var(--gold-light)); }

  .brand {
    position: absolute; left: 30px; top: 118px;
    display: flex; align-items: center; gap: 8px;
  }
  .brand__square { width: 14px; height: 14px; background: var(--gold); }
  .brand__name {
    font-size: 15px; font-weight: 600; color: var(--silver);
    text-transform: uppercase; letter-spacing: .08em; line-height: 1.2;
  }

  .contact {
    position: absolute; left: 30px; top: 182px;
    color: var(--white); font-size: 12.5px; line-height: 1.45;
  }
  .contact__address { margin-bottom: 10px; }
  .contact__line { display: flex; align-items: center; gap: 8px; }
  .contact__icon { width: 12px; height: 12px; flex: none; }

  .emblem {
    position: absolute; right: 26px; bottom: 34px;
    font-size: 38px; font-weight: 700; line-height: 1.05;
    color: var(--emboss); text-align: right; text-transform: uppercase;
  }
</style>
</head>
<body>
<main class="canvas">

  <section class="card card--back" aria-label="Card back">
    <div class="back-pattern" role="img" aria-label="Repeating tonal grey brand pattern across the card back"></div>
    <div class="back-mark">
      <span class="back-mark__square"></span>
      <span>Renwick Tolliver Construction</span>
    </div>
  </section>

  <section class="card card--front" aria-label="Card front">
    <div class="person">
      <div class="person__text">
        <p class="person__name"><span class="person__first">Lionel</span> <span class="person__last">Ashby</span></p>
        <p class="person__role">Managing Director</p>
      </div>
      <span class="person__bar"></span>
    </div>

    <div class="emblem">Renwick<br>Tolliver</div>

    <div class="brand">
      <span class="brand__square"></span>
      <p class="brand__name">Renwick Tolliver<br>Construction</p>
    </div>

    <div class="contact">
      <p class="contact__address">Harrow Lane, Eastwick<br>Larkford, LK4 7QT</p>
      <p class="contact__line">
        <svg class="contact__icon" viewBox="0 0 24 24" aria-hidden="true"><path fill="var(--gold)" d="M6.6 10.8a15.1 15.1 0 0 0 6.6 6.6l2.2-2.2c.3-.3.7-.4 1-.2 1.1.4 2.3.6 3.6.6.6 0 1 .4 1 1V20c0 .6-.4 1-1 1A17 17 0 0 1 3 4c0-.6.4-1 1-1h3.5c.6 0 1 .4 1 1 0 1.3.2 2.5.6 3.6.1.3 0 .7-.2 1z"/></svg>
        0782 225 4961
      </p>
      <p class="contact__line">
        <svg class="contact__icon" viewBox="0 0 24 24" aria-hidden="true"><rect x="2" y="5" width="20" height="14" rx="2" fill="var(--gold)"/><path d="M3 6l9 7 9-7" fill="none" stroke="var(--card-black)" stroke-width="2"/></svg>
        info@renwick-tolliver.co.uk
      </p>
      <p class="contact__line">
        <svg class="contact__icon" viewBox="0 0 24 24" aria-hidden="true"><circle cx="12" cy="12" r="10" fill="var(--gold)"/><path d="M2 12h20M12 2c3 3 3 17 0 20M12 2c-3 3-3 17 0 20" fill="none" stroke="var(--card-black)" stroke-width="1.5"/></svg>
        www.renwick-tolliver.co.uk
      </p>
    </div>
  </section>

</main>
</body>
</html>
```